Veldmark Supplies Business Card

Professional business card that stand out to our potential customers. Front and back with clean modern design

Industry/Entity Type

Oil and gas

Contact Information for Business Card

Name, address, website , office phone and cell number

Requirements
Must have
• Editable files for each employee

```html
<!DOCTYPE html>
<html lang="en">
<head>
<meta charset="UTF-8">
<title>Veldmark Supplies Business Card</title>
<link rel="stylesheet" href="https://fonts.googleapis.com/css2?family=Poppins:wght@400;500;600;700&display=swap">
<style>
  :root {
    --page-bg: #e2e7e9;
    --brand-red: #e8272a;
    --brand-blue: #17aed3;
    --copper: #f7cdb5;
    --card-light: #f0f0f0;
    --ink: #1e1e1e;
  }
  * { margin: 0; padding: 0; box-sizing: border-box; }
  html, body {
    width: 1200px; height: 960px; overflow: hidden;
    background: var(--page-bg);
    font-family: "Poppins", sans-serif;
  }
  .card {
    position: absolute; left: 250px; width: 701px; height: 400px;
  }
  .card-front { top: 73px; background: var(--brand-red); }
  .card-back { top: 513px; background: var(--card-light); }

  .front-brand {
    position: absolute; left: 0; right: 0; top: 160px;
    display: flex; align-items: center; justify-content: center; gap: 16px;
  }
  .front-brand .brand-square {
    width: 46px; height: 46px; background: var(--copper);
  }
  .front-brand .brand-name {
    color: var(--copper); font-weight: 600; font-size: 36px; letter-spacing: 2px;
  }

  .back-brand {
    position: absolute; left: 27px; top: 40px; width: 222px;
    display: flex; flex-direction: column; align-items: center; gap: 26px;
  }
  .back-brand .brand-square {
    width: 84px; height: 84px; background: var(--brand-red);
  }
  .back-brand .brand-name {
    color: var(--brand-red); font-weight: 600; font-size: 20px; letter-spacing: 1px; white-space: nowrap;
  }

  .person {
    position: absolute; right: 24px; top: 26px; text-align: right;
  }
  .person-name { font-size: 33px; line-height: 1.15; }
  .person-name .first { color: var(--brand-red); font-weight: 700; }
  .person-name .last { color: var(--brand-blue); font-weight: 400; }
  .person-title { color: var(--ink); font-size: 18px; font-weight: 500; margin-top: 2px; }
  .accent-bar {
    position: absolute; right: 0; top: 30px; width: 19px; height: 61px; background: var(--brand-red);
  }

  .address {
    position: absolute; left: 24px; top: 218px;
    color: var(--brand-red); font-size: 18px; line-height: 24px;
  }
  .contact-list {
    position: absolute; left: 24px; top: 284px; list-style: none;
  }
  .contact-list li {
    display: flex; align-items: center; gap: 12px;
    height: 23px; font-size: 18px; color: var(--ink);
  }
  .contact-list svg { width: 16px; height: 16px; flex: none; }
</style>
</head>
<body>
  <section class="card card-front">
    <div class="front-brand">
      <span class="brand-square"></span>
      <span class="brand-name">VELDMARK SUPPLIES</span>
    </div>
  </section>

  <section class="card card-back">
    <div class="back-brand">
      <span class="brand-square"></span>
      <span class="brand-name">VELDMARK SUPPLIES</span>
    </div>

    <div class="person">
      <div class="person-name"><span class="first">Mirela</span> <span class="last">Hanskova</span></div>
      <div class="person-title">Co-Founder &amp; CEO</div>
    </div>
    <div class="accent-bar"></div>

    <p class="address">482 Ashgrove Lane,<br>Millbrook, WI 53012</p>

    <ul class="contact-list">
      <li>
        <svg viewBox="0 0 16 16" aria-hidden="true"><path d="M3.5 1.5l2.5 2.5-1.5 2c.8 2 2.5 3.7 4.5 4.5l2-1.5 2.5 2.5-1.8 1.8C7.5 13 3 8.5 1.7 3.3z" fill="#e8272a"/></svg>
        (555) 214-6930
      </li>
      <li>
        <svg viewBox="0 0 16 16" aria-hidden="true"><rect x="4" y="1" width="8" height="14" rx="1.5" fill="none" stroke="#17aed3" stroke-width="1.6"/><circle cx="8" cy="8" r="1.6" fill="#17aed3"/></svg>
        (555) 318-4471
      </li>
      <li>
        <svg viewBox="0 0 16 16" aria-hidden="true"><circle cx="8" cy="8" r="7" fill="#e8272a"/><path d="M1 8h14M8 1c-3 3-3 11 0 14M8 1c3 3 3 11 0 14" stroke="#f0f0f0" stroke-width="1" fill="none"/></svg>
        www.veldmark-supply.com
      </li>
      <li>
        <svg viewBox="0 0 16 16" aria-hidden="true"><rect x="1" y="4" width="14" height="10" fill="#17aed3"/><path d="M1 4l7 5 7-5" stroke="#f0f0f0" stroke-width="1.2" fill="none"/></svg>
        info@veldmark-supply.com
      </li>
    </ul>
  </section>
</body>
</html>
```